Business Card for: Bramwell Financial Advisory Services Inc.

provide strategic financial advisory services to companies in the areas of corporate finance, mergers and acquisitions, executive coaching and strategic planning

Target Market(s)

Companies, banks, accountants, lawyers

Industry/Entity Type

High end business consulting in corporate finance, mergers and acquisitions, consulting

Contact Information for Business Card

Name of company, Name: xxxxxx xxxxxx , CEO, - phone number: 1-xxx-xxx-xxxx, - email address,

Requirements
Must have
• Must be professional and simple.
Nice to have
• simple, straight graphics, must give the impression that we are trustworthy, professional, competent
Should not have
• loud colors, loud design features

```html
<!DOCTYPE html>
<html lang="en">
<head>
<meta charset="utf-8">
<title>Bramwell Financial Advisory Services Inc. – Business Card</title>
<link href="https://fonts.googleapis.com/css2?family=Tinos:wght@400;700&display=swap" rel="stylesheet">
<style>
  :root {
    --navy: #002866;
    --orange: #ff6a0d;
    --ink: #1a1a1a;
    --paper: #ffffff;
    --backdrop: #9a9a9a;
  }
  * { box-sizing: border-box; margin: 0; padding: 0; }
  html, body { width: 1200px; height: 1059px; overflow: hidden; }
  body {
    background: var(--backdrop);
    font-family: "Tinos", "Times New Roman", serif;
    color: var(--ink);
    position: relative;
  }
  .card {
    position: absolute;
    left: 255px;
    width: 700px;
    height: 400px;
    border-radius: 26px;
    overflow: hidden;
  }
  .card--front { top: 84px; background: var(--paper); }
  .card--back { top: 570px; height: 404px; background: var(--navy); }

  .company-name {
    position: absolute;
    font-weight: 700;
    text-transform: uppercase;
    text-align: center;
    line-height: 1.15;
    font-size: 30px;
    letter-spacing: 1.5px;
    white-space: nowrap;
  }
  .card--front .company-name {
    left: 0; right: 0; top: 56px;
    color: var(--navy);
  }
  .card--back .company-name {
    left: 60px; right: 0; top: 168px;
    color: var(--paper);
  }

  .person { position: absolute; left: 41px; top: 198px; }
  .person__name { font-size: 26px; font-weight: 700; color: var(--navy); }
  .person__role { font-size: 17px; margin-top: 4px; }

  .divider {
    position: absolute; left: 41px; width: 618px; top: 269px;
    height: 1.5px; background: var(--ink);
  }

  .contact-list { position: absolute; left: 41px; top: 283px; list-style: none; }
  .contact-list li {
    display: flex; align-items: center; height: 30px;
    font-size: 18px;
  }
  .contact-list svg { width: 18px; height: 18px; margin-right: 17px; flex: none; }

  .address {
    position: absolute; right: 41px; top: 307px;
    text-align: right; font-size: 18px; line-height: 25px;
  }

  .footer-band { position: absolute; left: 0; bottom: 0; width: 700px; height: 14px; }
</style>
</head>
<body>

<section class="card card--front" aria-label="Card front">
  <p class="company-name">Bramwell<br>Financial Advisory Services Inc.</p>

  <div class="person">
    <p class="person__name">Daniel Hartwell</p>
    <p class="person__role">CEO</p>
  </div>

  <div class="divider"></div>

  <ul class="contact-list">
    <li>
      <svg viewBox="0 0 24 24" aria-hidden="true"><path fill="var(--orange)" d="M6.6 10.8a15.1 15.1 0 0 0 6.6 6.6l2.2-2.2c.3-.3.7-.4 1-.2 1.1.4 2.3.6 3.6.6.6 0 1 .4 1 1V20c0 .6-.4 1-1 1A17 17 0 0 1 3 4c0-.6.4-1 1-1h3.5c.6 0 1 .4 1 1 0 1.3.2 2.5.6 3.6.1.3 0 .7-.2 1z"/></svg>
      1-555-204-7718
    </li>
    <li>
      <svg viewBox="0 0 24 24" aria-hidden="true"><rect x="2" y="5" width="20" height="14" fill="var(--orange)"/><path d="M2 5l10 8 10-8" fill="none" stroke="#fff" stroke-width="1.8"/></svg>
      info@bramwellfa.com
    </li>
    <li>
      <svg viewBox="0 0 24 24" aria-hidden="true"><circle cx="12" cy="12" r="10" fill="none" stroke="var(--orange)" stroke-width="2.4"/><path d="M12 2v20M2 12h20" stroke="var(--orange)" stroke-width="1.6"/></svg>
      www.bramwellfa.com
    </li>
  </ul>

  <p class="address">88, Kingsley Avenue<br>30917, Westbrook</p>

  <svg class="footer-band" viewBox="0 0 700 14" preserveAspectRatio="none" aria-hidden="true">
    <polygon points="0,0 341,0 348,14 0,14" fill="var(--orange)"/>
    <polygon points="347,0 700,0 700,14 355,14" fill="var(--navy)"/>
  </svg>
</section>

<section class="card card--back" aria-label="Card back">
  <p class="company-name">Bramwell<br>Financial Advisory Services Inc.</p>
</section>

</body>
</html>
```